Business card design needed

I run a Beautician studio (for 7 years now)
I offer
- Velmo Body Sugaring
- Ruby Glaze
- Nails
- Facials
- Manicure
- Foot Treatment
It might not be necessary to list all those treatments?
Maybe the link to the Website is sufficient?
I leave that up to you ...
(more info on www.FernAndDewByLenka.com.au)
Velmo BodySugaring is our biggest success, It replaces waxing.
I would like to incorporate the logo into the Business Card.
We had many complaints regarding our old Business Cards as the Phone Number was to small.
On the backside, we would like a "your next Appointment" section.
Looking forward to you Design, cheers ... Lenka
Industry/Entity Type
Business
Contact Information for Business Card
Fern by Dew by Lenka
14 Korrin Sqr 3942 Tallowvale
www.FernAndDewByLenka.com.au
03 9481 2267

```html
<!DOCTYPE html>
<html lang="en">
<head>
<meta charset="utf-8">
<title>Fern by Dew by Lenka – Business Cards</title>
<link rel="stylesheet" href="https://fonts.googleapis.com/css2?family=Arimo:wght@400;700&family=Cinzel:wght@500&family=Open+Sans:wght@400;600&family=Tinos:wght@700&display=swap">
<style>
:root{
  --backdrop:#1c1c1c;
  --card:#ffffff;
  --ink:#1a1a1a;
  --muted:#444444;
  --green:#1f8a3a;
  --deep-green:#1d5a33;
  --orange-top:#f0a020;
  --orange-bottom:#e85a10;
  --sun:#f2a321;
  --line:#555555;
  --ghost:rgba(230,150,40,.08);
}
*{box-sizing:border-box;margin:0;padding:0}
html,body{width:1200px;height:728px;overflow:hidden;background:var(--backdrop)}
.sheet{position:relative;width:1200px;height:728px}
.card{position:absolute;width:541px;height:308px;background:var(--card);overflow:hidden;color:var(--ink)}
.card--front{left:41px;top:37px}
.card--appointment-a{left:615px;top:37px}
.card--back{left:41px;top:380px}
.card--appointment-b{left:623px;top:384px}
.ghost-name{position:absolute;left:0;right:0;top:170px;text-align:center;font-family:"Tinos",serif;font-size:60px;letter-spacing:8px;color:var(--ghost);white-space:nowrap}
.ghost-sun{position:absolute;left:185px;top:60px;width:170px;height:170px;border-radius:50%;background:var(--ghost)}

/* front */
.studio-name{position:absolute;left:0;right:0;top:32px;text-align:center;font-family:"Tinos",serif;font-weight:700;font-size:33px;letter-spacing:.5px;
  background:linear-gradient(var(--orange-top),var(--orange-bottom));-webkit-background-clip:text;background-clip:text;color:transparent}
.contact{position:absolute;left:36px;font-family:"Arimo",sans-serif;display:flex;align-items:center;gap:7px;white-space:nowrap}
.contact--phone{top:108px;font-size:16.5px}
.contact--web{top:136px;font-size:14px}
.contact--address{top:172px;font-size:14px;color:var(--muted)}
.contact svg{width:15px;height:15px}
.treatments-title{position:absolute;left:36px;top:220px;font-family:"Arimo",sans-serif;font-weight:700;font-size:17px;color:var(--green);letter-spacing:.5px}
.treatments{position:absolute;left:36px;top:244px;display:grid;grid-template-columns:176px auto;row-gap:3px;font-family:"Arimo",sans-serif;font-size:14.5px;list-style:none;white-space:nowrap}

/* appointment */
.appt-title{position:absolute;left:36px;top:52px;font-family:"Cinzel",serif;font-size:18px;color:var(--deep-green);letter-spacing:.5px}
.appt-brand{position:absolute;right:50px;top:18px;display:flex;flex-direction:column;align-items:center;gap:6px}
.appt-brand .dot{width:34px;height:34px;border-radius:50%;background:var(--sun)}
.appt-brand .word{font-family:"Tinos",serif;font-size:12px;letter-spacing:2px;color:var(--ink)}
.field-row{position:absolute;left:36px;font-family:"Open Sans",sans-serif;font-size:15px;color:var(--ink);display:flex;align-items:flex-end;gap:8px;white-space:nowrap}
.field-row .dotline{display:inline-block;border-bottom:1px dotted var(--line);height:1px;margin-bottom:5px}
.field-row .rule{display:inline-block;border-bottom:1px solid var(--line);height:1px;margin-bottom:5px}
.row-name{top:89px}
.row-date{top:127px}
.row-next{top:164px;align-items:center}
.box{display:inline-block;border:1px solid var(--line);height:21px}
.row-days{position:absolute;left:33px;top:206px;display:flex;align-items:center;gap:7px;font-family:"Arimo",sans-serif;font-weight:700;font-size:14.5px;color:var(--muted);white-space:nowrap}
.row-days .box{width:34px;height:20px;margin-right:3px}
.appt-note{position:absolute;left:32px;top:250px;width:468px;font-family:"Open Sans",sans-serif;font-size:13px;line-height:18px;color:var(--ink)}

/* back */
.back-brand{position:absolute;left:0;right:0;top:28px;display:flex;flex-direction:column;align-items:center}
.back-brand .dot{width:92px;height:92px;border-radius:50%;background:linear-gradient(var(--orange-top),var(--orange-bottom))}
.back-brand .word{margin-top:14px;font-family:"Tinos",serif;font-size:24px;letter-spacing:3px;color:var(--ink);white-space:nowrap}
.back-web{position:absolute;left:0;right:0;top:208px;text-align:center;font-family:"Open Sans",sans-serif;font-size:14.5px;letter-spacing:2px}
.hours-title{position:absolute;left:0;right:0;top:240px;text-align:center;font-family:"Open Sans",sans-serif;font-weight:600;font-size:20px;letter-spacing:1.5px;color:var(--muted)}
.hours{position:absolute;left:0;right:0;top:276px;text-align:center;font-family:"Open Sans",sans-serif;font-weight:600;font-size:15.5px;color:var(--muted);white-space:nowrap}
.hours .sep{color:#aaa;margin:0 8px}
</style>
</head>
<body>
<main class="sheet">

  <section class="card card--front">
    <div class="ghost-sun"></div>
    <div class="ghost-name">VELMO</div>
    <h1 class="studio-name">FERN BY DEW BY LENKA</h1>
    <p class="contact contact--phone">
      <svg viewBox="0 0 16 16" aria-hidden="true"><circle cx="8" cy="8" r="7" fill="none" stroke="#1f8a3a" stroke-width="1.4"/><path d="M5.5 4.5c-.8.8 0 3 1.5 4.5s3.7 2.3 4.5 1.5l-1.3-1.3-1 .6c-.8-.4-1.6-1.2-2-2l.6-1z" fill="#1f8a3a"/></svg>
      03 9481 2267</p>
    <p class="contact contact--web">
      <svg viewBox="0 0 16 16" aria-hidden="true"><circle cx="8" cy="8" r="6.5" fill="none" stroke="#1f8a3a" stroke-width="1.3"/><ellipse cx="8" cy="8" rx="3" ry="6.5" fill="none" stroke="#1f8a3a" stroke-width="1"/><path d="M1.5 8h13" stroke="#1f8a3a" stroke-width="1"/></svg>
      www.FernAndDewByLenka.com.au</p>
    <p class="contact contact--address">14 Korrin Sqr 3942 Tallowvale</p>
    <h2 class="treatments-title">Treatments offer</h2>
    <ul class="treatments">
      <li>• Velmo Body Sugaring</li><li>• Facials • Manicure</li>
      <li>• Ruby Glaze • Nails</li><li>• Foot Treatment</li>
    </ul>
  </section>

  <section class="card card--appointment-a">
    <div class="appt-brand"><span class="dot"></span><span class="word">VELMO</span></div>
    <h2 class="appt-title">YOUR APPOINTMENT</h2>
    <p class="field-row row-name">Name : <span class="dotline" style="width:290px"></span></p>
    <p class="field-row row-date">Date : <span class="rule" style="width:96px;margin-left:12px"></span> Time : <span class="rule" style="width:90px"></span> am / pm</p>
    <p class="field-row row-next">Next Appointment <span class="box" style="width:96px"></span><span class="box" style="width:96px;margin-left:24px"></span></p>
    <p class="row-days">MON <span class="box"></span> TUE <span class="box"></span> WED <span class="box"></span> THU <span class="box"></span> FRI <span class="box"></span> SAT <span class="box"></span></p>
    <p class="appt-note">It would be appreciated if 24 hours notice could be given if you are unable to attend an appointment</p>
  </section>

  <section class="card card--back">
    <div class="back-brand"><span class="dot"></span><span class="word">VELMO BODY SUGARING</span></div>
    <p class="back-web">www.FernAndDewByLenka.com.au</p>
    <h2 class="hours-title">Hours of Operation</h2>
    <p class="hours">Mon - Fri: 7.30am - 7.00pm<span class="sep">|</span>Saturday: 7.30am - 12.00pm</p>
  </section>

  <section class="card card--appointment-b">
    <div class="ghost-sun" style="left:190px;top:20px"></div>
    <div class="ghost-name" style="top:180px">VELMO</div>
    <h2 class="appt-title">YOUR APPOINTMENT</h2>
    <p class="field-row row-name">Name : <span class="dotline" style="width:290px"></span></p>
    <p class="field-row row-date">Date : <span class="rule" style="width:96px;margin-left:12px"></span> Time : <span class="rule" style="width:90px"></span> am / pm</p>
    <p class="field-row row-next">Next Appointment <span class="box" style="width:96px"></span><span class="box" style="width:96px;margin-left:24px"></span></p>
    <p class="row-days">MON <span class="box"></span> TUE <span class="box"></span> WED <span class="box"></span> THU <span class="box"></span> FRI <span class="box"></span> SAT <span class="box"></span></p>
    <p class="appt-note">It would be appreciated if 24 hours notice could be given if you are unable to attend an appointment</p>
  </section>

</main>
</body>
</html>
```